Business card design for sustainable building and development company

Need a business card design for a new sustainable building and real estate development company in the San Francisco Bay area. Name of company is "Tovrin Advisors, LLC" and we provide "Sustainable building, energy and development services" for residential and non residential projects. We'd like the following colors used but not all area required: green, gray, blue. Design should communicate innovation, professionalism and sustainability. Our current website is www.tovrin-advisors.example. Another possible design idea is to have the following listed on the back of the card:
Certified: VERN QS, Eco Marker Rater, DOLM Rater, Terravue Inspector, KSO TQ Building Analyst. Its not a must but could be text that could be used for back of card. Overall, we are open to a simple, clean design and or one with more text than usual for a card.

Industry/Entity Type

Real Estate

Contact Information for Business Card

Name on card: Mark J. Halvik
Title for Name: Principal + Founder
Phone: 555.814.0627
Email: mhalvik@tovrin-advisors.example
Website: www.tovrin-advisors.example

Also, please add the following for address:
Ashford Vale, Merrow

Requirements
Nice to have
• If you can integrate the outline of a skyline on the backside of the card and if it looks good, I would like to see the design
Should not have
• a barcode;

```html
<!DOCTYPE html>
<html lang="en">
<head>
<meta charset="utf-8">
<title>Tovrin Advisors – Business Card</title>
<link href="https://fonts.googleapis.com/css2?family=Montserrat:wght@400;500;600;700&display=swap" rel="stylesheet">
<style>
  :root {
    --bg: #6a6a6a;
    --paper: #f3f3f1;
    --ink: #151515;
    --green: #5cb83a;
    --text-dark: #2b2b2b;
    --text-light: #e9e9e9;
    --text-muted: #7a7a7a;
  }
  * { margin: 0; padding: 0; box-sizing: border-box; }
  html, body { width: 1200px; height: 1029px; overflow: hidden; }
  body {
    background: var(--bg);
    font-family: "Montserrat", sans-serif;
    position: relative;
  }
  .card {
    position: absolute;
    width: 740px;
    height: 423px;
    background: var(--paper);
    box-shadow: 0 14px 30px rgba(0,0,0,.35);
    overflow: hidden;
  }
  /* Front */
  .card--front { left: 400px; top: 60px; }
  .brand {
    position: absolute;
    display: flex;
    align-items: center;
    gap: 16px;
  }
  .brand__mark {
    width: 86px; height: 86px;
    border-radius: 50%;
    background: var(--green);
    flex: none;
  }
  .brand__name {
    color: var(--green);
    font-weight: 700;
    font-size: 40px;
    line-height: 1;
    letter-spacing: .2px;
    white-space: nowrap;
  }
  .brand__tagline {
    margin-top: 6px;
    color: var(--text-dark);
    font-weight: 600;
    font-size: 9.5px;
    letter-spacing: .4px;
    text-transform: uppercase;
    white-space: nowrap;
  }
  .card--front .brand { left: 160px; top: 118px; }
  .front__rule {
    position: absolute; left: 0; right: 0; top: 262px;
    height: 9px; background: var(--green);
  }
  .front__band {
    position: absolute; left: 0; right: 0; top: 271px; bottom: 0;
    background: var(--ink);
  }
  .front__url {
    position: absolute; left: 0; right: 0; top: 358px;
    text-align: center;
    color: var(--text-muted);
    font-size: 12px;
    letter-spacing: 1px;
    text-transform: uppercase;
  }
  /* Back */
  .card--back { left: 90px; top: 560px; }
  .back__panel {
    position: absolute; left: 0; top: 0; bottom: 0; width: 404px;
    background: var(--paper);
  }
  .card--back .brand { left: 28px; top: 150px; gap: 14px; }
  .card--back .brand__mark { width: 70px; height: 70px; }
  .card--back .brand__name { font-size: 29px; }
  .card--back .brand__tagline { font-size: 8px; letter-spacing: .3px; }
  .back__strip {
    position: absolute; left: 404px; top: 0; bottom: 0; width: 50px;
    background: var(--green);
  }
  .back__icons {
    position: absolute; left: 0; right: 0; top: 186px;
    display: flex; flex-direction: column; align-items: center; gap: 12px;
  }
  .back__icons svg { width: 16px; height: 16px; fill: #fff; }
  .back__icons .icon-person { width: 22px; height: 22px; margin-bottom: 14px; }
  .back__dark {
    position: absolute; left: 454px; right: 0; top: 0; bottom: 0;
    background: var(--ink);
  }
  .contact { position: absolute; left: 476px; top: 184px; right: 14px; }
  .contact__name {
    color: #fff; font-weight: 600; font-size: 23px; letter-spacing: 1px;
    text-transform: uppercase; white-space: nowrap;
  }
  .contact__name span { color: var(--green); font-weight: 400; }
  .contact__title {
    color: var(--text-muted); font-size: 9.5px; letter-spacing: 1px;
    text-transform: uppercase; margin: 3px 0 18px;
  }
  .contact__list { list-style: none; }
  .contact__list li {
    color: var(--text-light); font-size: 10.5px; letter-spacing: .6px;
    text-transform: uppercase; line-height: 23px; white-space: nowrap;
  }
</style>
</head>
<body>
  <section class="card card--front">
    <div class="brand">
      <div class="brand__mark"></div>
      <div>
        <div class="brand__name">Tovrin Advisors</div>
        <div class="brand__tagline">Green building, power &amp; planning services</div>
      </div>
    </div>
    <div class="front__rule"></div>
    <div class="front__band"></div>
    <div class="front__url">www.tovrin-advisors.example</div>
  </section>

  <section class="card card--back">
    <div class="back__panel">
      <div class="brand">
        <div class="brand__mark"></div>
        <div>
          <div class="brand__name">Tovrin Advisors</div>
          <div class="brand__tagline">Green building, power &amp; planning services</div>
        </div>
      </div>
    </div>
    <div class="back__strip">
      <div class="back__icons">
        <svg class="icon-person" viewBox="0 0 24 24"><circle cx="12" cy="7" r="5"/><path d="M2 23c0-6 4.5-9 10-9s10 3 10 9z"/></svg>
        <svg viewBox="0 0 24 24"><path d="M6.6 10.8a15 15 0 0 0 6.6 6.6l2.2-2.2c.3-.3.7-.4 1-.2 1.1.4 2.3.6 3.6.6.6 0 1 .4 1 1V20c0 .6-.4 1-1 1A17 17 0 0 1 3 4c0-.6.4-1 1-1h3.5c.6 0 1 .4 1 1 0 1.3.2 2.5.6 3.6.1.3 0 .7-.2 1z"/></svg>
        <svg viewBox="0 0 24 24"><path d="M2 5h20v14H2z" fill="none" stroke="#fff" stroke-width="2"/><path d="M2 5l10 8 10-8" fill="none" stroke="#fff" stroke-width="2"/></svg>
        <svg viewBox="0 0 24 24"><path d="M3 4h18v12H3z" fill="none" stroke="#fff" stroke-width="2"/><path d="M9 20h6v-2H9z"/></svg>
        <svg viewBox="0 0 24 24"><path d="M12 2a7 7 0 0 0-7 7c0 5 7 13 7 13s7-8 7-13a7 7 0 0 0-7-7zm0 9.5A2.5 2.5 0 1 1 12 6.5a2.5 2.5 0 0 1 0 5z"/></svg>
      </div>
    </div>
    <div class="back__dark"></div>
    <div class="contact">
      <div class="contact__name">Mark J. <span>Halvik</span></div>
      <div class="contact__title">Principal/Owner</div>
      <ul class="contact__list">
        <li>555.814.0627</li>
        <li>mhalvik@tovrin-advisors.example</li>
        <li>www.tovrin-advisors.example</li>
        <li>Ashford Vale, Merrow</li>
      </ul>
    </div>
  </section>
</body>
</html>
```